Tech Savy small Business accountant business card design

We need a business card for a new company based in the cloud. We provide tax, business advisory, accounting, information technology solutions and back office functions to small businesses. We offer fixed fee packages with add on services as you need them. By harnessing technology we simplify small business operational processes providing valuable time and information for small business owners to grow their business. In the logo (bluvoria) we want to be able to see bluv and experts. The final design should communicate achieving growth dreams and balance (ie life and $).
Updates
This project has been temporarily placed on hold until I finalize "Tech Savy small Business accountant needs a logo". I invite all designers to submit on this logo project. Once my logo is finalized I will resume this business card contest. Thanks Added Wednesday, March 19, 2014
This project has been temporarily placed on hold until I finalize "Tech Savy small Business accountant logo". I invite all designers to submit on this logo project. Once my logo is finalized I will resume this business card contest. Thanks Added Thursday, March 20, 2014
Target Market(s)
Small Business (Revenue $500,000, more than 3 employees) owners.
Industry/Entity Type
Small Business
Contact Information for Business Card
Marcy Elwind (Principal)
Accountant, Tax Agent.
TEL | 0417 683 912
EMAIL | Marcy.Elwind@bluvoria.com.au
WEB | www.bluvoria.com.au
Look and feel

```html
<!DOCTYPE html>
<html lang="en">
<head>
<meta charset="utf-8">
<title>bluvoria business card</title>
<link rel="stylesheet" href="https://fonts.googleapis.com/css2?family=Open+Sans:wght@400;600;700&display=swap">
<style>
  :root {
    --page: #eceef0;
    --card: #ffffff;
    --blue: #1e88d2;
    --blue-dark: #1667ad;
    --grey: #77797c;
    --grey-dark: #5e6063;
    --text-grey: #6d6f72;
    --shadow: rgba(0, 0, 0, 0.18);
  }
  * { box-sizing: border-box; margin: 0; padding: 0; }
  html, body {
    width: 1200px; height: 913px; overflow: hidden;
    background: var(--page);
    font-family: "Open Sans", Arial, sans-serif;
  }
  .sheet {
    position: relative; width: 1200px; height: 913px;
    display: flex; flex-direction: column; align-items: center; justify-content: center; gap: 56px;
  }
  .card {
    position: relative; width: 620px; height: 378px;
    background: var(--card);
    box-shadow: 0 6px 22px var(--shadow);
    overflow: hidden;
  }
  .card__bands { position: absolute; inset: 0; width: 100%; height: 100%; }
  .brand { position: absolute; }
  .brand__name {
    display: block; font-weight: 700; color: var(--blue);
    letter-spacing: -1px; line-height: 1;
  }
  .brand__tagline {
    display: block; font-weight: 600; color: var(--text-grey); letter-spacing: 0.5px;
    white-space: nowrap;
  }
  /* contact side */
  .card--contact .brand { left: 34px; top: 40px; }
  .card--contact .brand__name { font-size: 58px; }
  .card--contact .brand__tagline { font-size: 15px; margin-top: 2px; }
  .person {
    position: absolute; right: 34px; top: 48px; text-align: right;
  }
  .person__name { font-size: 21px; font-weight: 700; color: var(--blue); letter-spacing: 0.5px; }
  .person__role {
    font-size: 13px; color: var(--text-grey); padding-bottom: 3px;
    border-bottom: 1px solid var(--blue);
  }
  .divider {
    position: absolute; left: 34px; top: 186px; width: 380px; height: 1px; background: var(--blue);
  }
  .contact { position: absolute; left: 34px; top: 196px; list-style: none; }
  .contact__item {
    display: flex; align-items: center; gap: 10px;
    font-size: 15px; color: var(--blue); line-height: 24px;
  }
  .contact__icon { width: 13px; height: 13px; fill: none; stroke: var(--grey-dark); stroke-width: 1.6; }
  /* logo side */
  .card--logo .brand { left: 70px; top: 112px; }
  .card--logo .brand__name { font-size: 92px; }
  .card--logo .brand__tagline { font-size: 22px; margin-top: 4px; }
</style>
</head>
<body>
<main class="sheet">

  <section class="card card--contact" aria-label="Card back with contact details">
    <svg class="card__bands" viewBox="0 0 620 378" preserveAspectRatio="none" aria-hidden="true">
      <polygon points="380,250 620,250 620,378 420,378" fill="var(--grey)"/>
      <polygon points="0,338 396,338 408,378 0,378" fill="var(--blue)"/>
      <polygon points="372,262 392,262 414,310 392,358 372,358 394,310" fill="var(--grey-dark)"/>
      <polygon points="360,300 376,300 390,330 376,358 360,358 374,330" fill="var(--blue-dark)"/>
    </svg>
    <div class="brand">
      <span class="brand__name">bluvoria</span>
      <span class="brand__tagline">Cloud tax and advice for small firms</span>
    </div>
    <div class="person">
      <p class="person__name">MARCY ELWIND (Principal)</p>
      <p class="person__role">Accountant, Tax Agent</p>
    </div>
    <div class="divider"></div>
    <ul class="contact">
      <li class="contact__item">
        <svg class="contact__icon" viewBox="0 0 14 14"><path d="M3 1l2 3-1.5 1.5a8 8 0 0 0 5 5L10 9l3 2-1.5 2.5C6 13 1 8 .5 2.5z"/></svg>
        0417 683 912
      </li>
      <li class="contact__item">
        <svg class="contact__icon" viewBox="0 0 14 14"><circle cx="7" cy="7" r="6"/><path d="M1 7h12M7 1c3 3 3 9 0 12M7 1c-3 3-3 9 0 12"/></svg>
        www.bluvoria.com.au
      </li>
      <li class="contact__item">
        <svg class="contact__icon" viewBox="0 0 14 14"><rect x="1" y="3" width="12" height="8"/><path d="M1 3l6 5 6-5"/></svg>
        Marcy.Elwind@bluvoria.com.au
      </li>
    </ul>
  </section>

  <section class="card card--logo" aria-label="Card front with brand name">
    <svg class="card__bands" viewBox="0 0 620 378" preserveAspectRatio="none" aria-hidden="true">
      <polygon points="380,250 620,250 620,378 420,378" fill="var(--grey)"/>
      <polygon points="0,338 396,338 408,378 0,378" fill="var(--blue)"/>
      <polygon points="372,262 392,262 414,310 392,358 372,358 394,310" fill="var(--grey-dark)"/>
      <polygon points="360,300 376,300 390,330 376,358 360,358 374,330" fill="var(--blue-dark)"/>
    </svg>
    <div class="brand">
      <span class="brand__name">bluvoria</span>
      <span class="brand__tagline">Cloud tax and advice for small firms</span>
    </div>
  </section>

</main>
</body>
</html>
```